Web Developer Needs a Business Card Design

I need a personal business card design that represents me as a web developer for potential employers. I would like the background to be a dark color on the front for contrast with my logo and name. The back will have all my information along with a smaller version of the logo. I want something with a modern look and feel, not too conservative. This will be used for potential employers and freelance work.

Industry/Entity Type

Business

Contact Information for Business Card

Front should have my logo and name. The back should have all my personal information which would include: name: Tom Varulek, phone: 570-614-3098, email: tomvarulek@quillbox.net, website url: www.tomvarulek.net, logo, web developer.

Font styles to use
Sans Serif

Requirements
Must have
• Must include my logo. The color palette base color will be the logo color.

```html
<!DOCTYPE html>
<html lang="en">
<head>
<meta charset="utf-8">
<title>Tom Varulek — Business Card</title>
<link rel="stylesheet" href="https://fonts.googleapis.com/css2?family=Lato:wght@400;700&display=swap">
<style>
  :root {
    --brand: #2a8a74;
    --brand-light: #33917d;
    --brand-dark: #146b56;
    --paper: #ffffff;
    --ink: #1e1e1e;
    --backdrop: #e8e8e8;
  }
  * { box-sizing: border-box; margin: 0; padding: 0; }
  html, body {
    width: 1200px; height: 720px; overflow: hidden;
    background: var(--backdrop);
    font-family: "Lato", Arial, sans-serif;
  }
  .canvas { position: relative; width: 1200px; height: 720px; }

  .card {
    position: absolute; top: 242px;
    width: 419px; height: 238px;
    border-radius: 6px; overflow: hidden;
  }
  .card--info { left: 179px; background: var(--paper); }
  .card--brand {
    left: 609px;
    background: linear-gradient(160deg, var(--brand-light) 0%, var(--brand-dark) 100%);
  }

  .split-ring {
    position: absolute; width: 228px; height: 228px;
    top: 4px; border-radius: 50%;
  }
  .card--info .split-ring { left: 314px; border: 17px solid var(--brand); }
  .card--brand .split-ring {
    left: -116px; border: 17px solid var(--paper);
    box-shadow: 0 0 0 4px var(--brand-dark);
  }

  .wordmark {
    position: absolute; left: 25px; top: 22px;
    display: flex; align-items: center; gap: 10px;
  }
  .wordmark__ring {
    width: 48px; height: 48px; border-radius: 50%;
    border: 4px solid var(--brand);
  }
  .wordmark__name {
    color: var(--brand); font-weight: 700; font-size: 17px; letter-spacing: 2.2px;
  }

  .identity { position: absolute; left: 26px; top: 104px; }
  .identity__name { color: var(--brand); font-weight: 700; font-size: 16px; }
  .identity__role { color: var(--ink); font-size: 13px; margin-top: 1px; }

  .contacts {
    position: absolute; left: 26px; top: 156px; list-style: none;
  }
  .contacts li {
    display: flex; align-items: center; gap: 6px;
    color: var(--ink); font-size: 13.5px; line-height: 17px;
  }
  .contacts svg { width: 12px; height: 12px; fill: var(--brand); flex: none; }

  .brand-mark {
    position: absolute; left: 224px; top: 61px;
    width: 120px; height: 120px; border-radius: 50%;
    border: 8px solid var(--paper);
    display: flex; align-items: center; justify-content: center;
  }
  .brand-mark__name {
    color: var(--paper); font-weight: 700; font-size: 12px; letter-spacing: 1.2px;
  }
  .brand-url {
    position: absolute; left: 184px; width: 200px; top: 188px;
    text-align: center; white-space: nowrap;
    color: var(--paper); font-size: 13px; letter-spacing: 0.8px;
  }
</style>
</head>
<body>
<main class="canvas">
  <section class="card card--info" aria-label="Card back with contact details">
    <div class="split-ring"></div>
    <div class="wordmark">
      <span class="wordmark__ring"></span>
      <span class="wordmark__name">TOM VARULEK</span>
    </div>
    <div class="identity">
      <p class="identity__name">Tom Varulek</p>
      <p class="identity__role">Web Developer</p>
    </div>
    <ul class="contacts">
      <li>
        <svg viewBox="0 0 24 24" aria-hidden="true"><path d="M6.6 10.8a15.1 15.1 0 0 0 6.6 6.6l2.2-2.2c.3-.3.7-.4 1-.2 1.1.4 2.3.6 3.6.6.6 0 1 .4 1 1V20c0 .6-.4 1-1 1A17 17 0 0 1 3 4c0-.6.4-1 1-1h3.5c.6 0 1 .4 1 1 0 1.3.2 2.5.6 3.6.1.3 0 .7-.2 1z"/></svg>
        570-614-3098
      </li>
      <li>
        <svg viewBox="0 0 24 24" aria-hidden="true"><path d="M2 5h20v14H2zm2 2v.5l8 5 8-5V7l-8 5z"/></svg>
        tomvarulek@quillbox.net
      </li>
      <li>
        <svg viewBox="0 0 24 24" aria-hidden="true"><path d="M12 2a10 10 0 1 0 0 20 10 10 0 0 0 0-20zm6.9 6h-3a15 15 0 0 0-1.3-4A8 8 0 0 1 18.9 8zM12 4c.8 1.2 1.5 2.5 1.9 4h-3.8c.4-1.5 1.1-2.8 1.9-4zM4.3 14a8 8 0 0 1 0-4h3.4a16 16 0 0 0 0 4zm.8 2h3a15 15 0 0 0 1.3 4A8 8 0 0 1 5.1 16zm3-8h-3a8 8 0 0 1 4.3-4 15 15 0 0 0-1.3 4zM12 20c-.8-1.2-1.5-2.5-1.9-4h3.8c-.4 1.5-1.1 2.8-1.9 4zm2.3-6H9.7a14 14 0 0 1 0-4h4.6a14 14 0 0 1 0 4zm.3 6a15 15 0 0 0 1.3-4h3a8 8 0 0 1-4.3 4zm1.7-6a16 16 0 0 0 0-4h3.4a8 8 0 0 1 0 4z"/></svg>
        www.tomvarulek.net
      </li>
    </ul>
  </section>

  <section class="card card--brand" aria-label="Card front with name">
    <div class="split-ring"></div>
    <div class="brand-mark">
      <span class="brand-mark__name">TOM VARULEK</span>
    </div>
    <p class="brand-url">www.tomvarulek.net</p>
  </section>
</main>
</body>
</html>
```